We need professional looking business cards for our e-assessment business based in Europe. Our company is called Velmo.

You can just use sample name and addresses.

The colours we use are:

#70abe4 (blue)
#FF6600 (orange)

The back side should say: E-assessment made easy

This is the print-shop we are using. Please look at the link for info about formats: http://nl.prindavo.com/help/faq/using-my-own-artwork.html

Target market is education and large corporations

Business

```html
<!DOCTYPE html>
<html lang="en">
<head>
<meta charset="utf-8">
<title>Velmo business cards</title>
<link rel="stylesheet" href="https://fonts.googleapis.com/css2?family=Questrial&display=swap">
<style>
  :root {
    --orange: #ff6600;
    --orange-deep: #e8581a;
    --blue: #70abe4;
    --ink: #2b2b2b;
    --ink-soft: #4a4a4a;
    --card: #f7f7f7;
    --card-shade: #e4e4e4;
    --backdrop: #d9d7d3;
  }
  html, body {
    margin: 0;
    padding: 0;
    overflow: hidden;
  }
  body {
    width: 1200px;
    height: 871px;
    background: var(--backdrop);
    position: relative;
    font-family: "Questrial", "Century Gothic", sans-serif;
  }
  .card {
    position: absolute;
    width: 560px;
    height: 320px;
    background: linear-gradient(160deg, #ffffff 0%, var(--card) 55%, var(--card-shade) 100%);
    box-shadow: 0 10px 24px rgba(0, 0, 0, 0.22);
    box-sizing: border-box;
  }
  /* Back side */
  .card-back {
    left: 80px;
    top: 100px;
    display: flex;
    flex-direction: column;
    align-items: center;
    justify-content: center;
  }
  .back-mark {
    width: 170px;
    height: 170px;
    border-radius: 50%;
    background: var(--orange-deep);
    display: flex;
    align-items: center;
    justify-content: center;
    color: #ffffff;
    font-size: 40px;
    letter-spacing: 0.5px;
  }
  .tagline {
    margin-top: 26px;
    color: var(--blue);
    font-size: 19px;
    letter-spacing: 1.5px;
  }
  /* Front side */
  .card-front {
    left: 560px;
    top: 460px;
    padding: 34px 40px;
  }
  .brand {
    display: flex;
    align-items: center;
    gap: 18px;
  }
  .brand-dot {
    width: 62px;
    height: 62px;
    border-radius: 50%;
    background: var(--orange-deep);
    flex: none;
  }
  .brand-name {
    color: var(--ink);
    font-size: 64px;
    line-height: 1;
    letter-spacing: -1px;
  }
  .contact {
    position: absolute;
    right: 56px;
    bottom: 36px;
    font-size: 15px;
    line-height: 1.55;
    color: var(--ink-soft);
    letter-spacing: 0.8px;
  }
  .contact-name {
    font-size: 19px;
    color: var(--ink);
    margin-bottom: 2px;
    letter-spacing: 1.5px;
  }
  .contact-company {
    color: var(--orange);
  }
</style>
</head>
<body>
  <section class="card card-back" aria-label="Card back">
    <div class="back-mark">velmo</div>
    <p class="tagline">E-assessment made easy</p>
  </section>

  <section class="card card-front" aria-label="Card front">
    <div class="brand">
      <span class="brand-dot" aria-hidden="true"></span>
      <span class="brand-name">velmo</span>
    </div>
    <address class="contact" style="font-style: normal;">
      <div class="contact-name">Aren T Loddel</div>
      <div class="contact-company">velmo Inc</div>
      <div>18 Perrin Lane, Halvick</div>
      <div>QLD 4190</div>
    </address>
  </section>
</body>
</html>
```